Corvane Capital Business Cards

These are professional business cards that are for my family office.
Put fake emails and phone numbers as of now until I finalize those components. This family office controls my families investments, assets, and future. The cards should be professional.
..
.
.
.
I just uploaded another variation of a logo I would like to see as a business card to I am inbeteen which logo to use

Target Market(s)

business

Industry/Entity Type

business

Contact Information for Business Card

Professional, wealth related, finance related.

Requirements
Must have
• Logo

```html
<!DOCTYPE html>
<html lang="en">
<head>
<meta charset="utf-8">
<title>Corvane Capital Business Cards</title>
<link rel="stylesheet" href="https://fonts.googleapis.com/css2?family=Cinzel:wght@500;700&family=Montserrat:wght@600&family=Arimo&display=swap">
<style>
  :root {
    --navy: #1c1f2e;
    --white: #ffffff;
    --grey: #a8a7a9;
    --ink-soft: #454545;
    --ink: #2f2f2f;
    --backdrop: #d5d5d5;
  }
  * { margin: 0; padding: 0; box-sizing: border-box; }
  html, body { width: 1200px; height: 1000px; overflow: hidden; }
  body { background: var(--backdrop); position: relative; }

  .card { position: absolute; left: 285px; width: 802px; height: 457px; }
  .card--front { top: 31px; background: var(--navy); }
  .card--back { top: 511px; background: var(--white); }

  .front-emblem { position: absolute; left: 290px; top: 74px; width: 230px; height: 230px;
    border: 4px solid var(--white); border-radius: 50%; }
  .front-name { position: absolute; left: 0; right: 0; top: 330px; text-align: center;
    font-family: 'Cinzel', serif; font-weight: 500; font-size: 34px; color: var(--white); letter-spacing: 1px; }
  .front-web { position: absolute; left: 0; right: 0; top: 404px; text-align: center;
    font-family: 'Arimo', sans-serif; font-size: 19px; color: var(--white); letter-spacing: 3.2px; }

  .holder-name { position: absolute; left: 38px; top: 86px;
    font-family: 'Cinzel', serif; font-weight: 700; font-size: 30px; color: var(--navy); }
  .holder-role { position: absolute; left: 38px; top: 130px;
    font-family: 'Montserrat', sans-serif; font-weight: 600; font-size: 20px; color: var(--ink-soft); letter-spacing: .5px; }
  .holder-rule { position: absolute; left: 40px; top: 166px; width: 50px; height: 3px; background: var(--navy); }

  .contact-list { position: absolute; left: 40px; top: 212px; list-style: none;
    font-family: 'Arimo', sans-serif; font-size: 21px; color: var(--ink); }
  .contact-list li { display: flex; align-items: flex-start; gap: 9px; line-height: 32px; margin-bottom: 1px; }
  .contact-list svg { width: 24px; height: 24px; margin-top: 4px; flex: none; }

  .back-emblem { position: absolute; left: 525px; top: 119px; width: 160px; height: 160px;
    border: 3px solid var(--navy); border-radius: 50%; }
  .back-name { position: absolute; left: 440px; width: 330px; top: 292px; text-align: center;
    font-family: 'Cinzel', serif; font-weight: 500; font-size: 32px; color: var(--navy); }

  .band-dark { position: absolute; left: 0; top: 408px; width: 575px; height: 24px; background: var(--navy); }
  .band-grey { position: absolute; left: 630px; top: 408px; width: 172px; height: 24px; background: var(--grey); }
  .band-dot { position: absolute; left: 572px; top: 392px; width: 56px; height: 56px; border-radius: 50%;
    background: var(--white); border: 2px solid var(--navy); }
</style>
</head>
<body>
  <section class="card card--front">
    <div class="front-emblem"></div>
    <p class="front-name">Corvane Capital</p>
    <p class="front-web">WWW.CORVANECAP.COM</p>
  </section>

  <section class="card card--back">
    <h1 class="holder-name">ELLIOT MARSH</h1>
    <p class="holder-role">MANAGING DIRECTOR</p>
    <div class="holder-rule"></div>

    <ul class="contact-list">
      <li>
        <svg viewBox="0 0 24 24" aria-hidden="true"><rect x="1" y="1" width="22" height="22" rx="4" fill="var(--navy)"/><rect x="6" y="5" width="4" height="14" rx="1" fill="#fff"/><rect x="11" y="6" width="8" height="12" rx="1" fill="none" stroke="#fff" stroke-width="1.5"/><path d="M13 9h4M13 12h4M13 15h4" stroke="#fff" stroke-width="1.2"/></svg>
        <span>044-987 654 321</span>
      </li>
      <li>
        <svg viewBox="0 0 24 24" aria-hidden="true"><rect x="1" y="1" width="22" height="22" rx="4" fill="var(--navy)"/><path d="M5 12l14-6-5 13-2.5-5z" fill="none" stroke="#fff" stroke-width="1.6" stroke-linejoin="round"/></svg>
        <span>info@corvanecap.com</span>
      </li>
      <li>
        <svg viewBox="0 0 24 24" aria-hidden="true"><rect x="1" y="1" width="22" height="22" rx="4" fill="var(--navy)"/><path d="M12 19s-5-5-5-8.5a5 5 0 0 1 10 0C17 14 12 19 12 19z" fill="none" stroke="#fff" stroke-width="1.6"/><circle cx="12" cy="10.5" r="1.8" fill="#fff"/></svg>
        <span>4410 Harbor Light Pkwy,<br>210-B, FL 32541</span>
      </li>
    </ul>

    <div class="back-emblem"></div>
    <p class="back-name">Corvane Capital</p>

    <div class="band-dark"></div>
    <div class="band-grey"></div>
    <div class="band-dot"></div>
  </section>
</body>
</html>
```